Business Card for Field Lotus-Eco Friendly Organic Clothing Brand

We are looking for an amazing business card for our eco friendly, organic clothing brand. We are thinking maybe a business card with a peel off sticker on the back, since our hanging clothing tag is a peel off sticker on the back. I will attach our hang tag so we can make sure we stay in line with our design. I've also attached a bag we are doing because I do like the scattered emblem look as well.

```html
<!DOCTYPE html>
<html lang="en">
<head>
<meta charset="utf-8">
<title>Field Lotus – Business Card</title>
<link rel="stylesheet" href="https://fonts.googleapis.com/css2?family=Libre+Baskerville:wght@700&family=Montserrat:wght@700&family=Roboto:wght@400&display=swap">
<style>
  :root {
    --olive-dark: #262a1c;
    --olive: #343a27;
    --gold: #c9a43c;
    --paper: #f4f4f2;
    --ink: #2a2a2a;
    --stage: #e9e6df;
  }
  * { margin: 0; padding: 0; box-sizing: border-box; }
  html, body { width: 1200px; height: 902px; overflow: hidden; background: var(--stage); }
  .canvas { position: relative; width: 1200px; height: 902px; }
  .card {
    position: absolute; left: 240px; width: 720px; height: 411px;
    border-radius: 6px; overflow: hidden;
    box-shadow: 0 6px 18px rgba(0,0,0,.18);
  }
  /* back */
  .card--back { top: 30px; background: var(--olive-dark); }
  .back-pattern {
    position: absolute; inset: 0;
    background: radial-gradient(circle at 30% 40%, #3d3a22 0%, var(--olive-dark) 70%);
  }
  .back-frame {
    position: absolute; left: 110px; top: 145px; width: 500px; height: 121px;
    border: 4px solid var(--gold); background: var(--olive-dark);
    display: flex; align-items: center; justify-content: center;
  }
  .back-name {
    font-family: "Montserrat", sans-serif; font-weight: 700; font-size: 62px;
    color: var(--gold); white-space: nowrap;
  }
  /* front */
  .card--front { top: 461px; background: var(--paper); }
  .front-band { position: absolute; left: 0; top: 0; width: 100%; height: 165px; background: var(--olive-dark); }
  .tag {
    position: absolute; left: 250px; top: 55px; width: 330px; height: 150px;
    background: var(--olive); border: 3px solid var(--gold);
    border-radius: 18px; box-shadow: 0 0 0 6px var(--paper);
    display: flex; flex-direction: column; align-items: center; justify-content: center; gap: 8px;
  }
  .tag-row { display: flex; align-items: center; gap: 16px; }
  .tag-mark { width: 34px; height: 34px; background: var(--gold); }
  .tag-name {
    font-family: "Montserrat", sans-serif; font-weight: 700; font-size: 40px; color: var(--gold);
    white-space: nowrap;
  }
  .tag-url { font-family: "Roboto", sans-serif; font-size: 14px; color: var(--gold); }
  .person { position: absolute; left: 44px; bottom: 48px; color: var(--ink); }
  .person-name { font-family: "Libre Baskerville", serif; font-weight: 700; font-size: 30px; white-space: nowrap; }
  .person-title { font-family: "Roboto", sans-serif; font-size: 20px; margin-top: 4px; }
  .contact {
    position: absolute; left: 400px; top: 232px;
    border-left: 2px solid var(--ink); padding-left: 14px;
    list-style: none; font-family: "Roboto", sans-serif; font-size: 19px; color: var(--ink);
  }
  .contact li { display: flex; align-items: center; gap: 12px; height: 34px; white-space: nowrap; }
  .contact svg { width: 18px; height: 18px; flex: none; }
</style>
</head>
<body>
<div class="canvas">

  <section class="card card--back">
    <div class="back-pattern" role="img" aria-label="Decorative gold pattern on a dark olive ground"></div>
    <div class="back-frame"><span class="back-name">Field Lotus</span></div>
  </section>

  <section class="card card--front">
    <div class="front-band"></div>
    <div class="tag">
      <div class="tag-row">
        <span class="tag-mark"></span>
        <span class="tag-name">Field Lotus</span>
      </div>
      <span class="tag-url">www.fieldlotus.com</span>
    </div>

    <div class="person">
      <div class="person-name">Dana Marlow</div>
      <div class="person-title">Managing Director</div>
    </div>

    <ul class="contact">
      <li>
        <svg viewBox="0 0 18 18"><rect width="18" height="18" rx="2" fill="#2a2a2a"/><path d="M5 4l2 0 1 3-1.5 1a7 7 0 0 0 3.5 3.5L11 10l3 1v2a1 1 0 0 1-1 1A9 9 0 0 1 4 5a1 1 0 0 1 1-1z" fill="#fff"/></svg>
        (555) 014-2290
      </li>
      <li>
        <svg viewBox="0 0 18 18"><rect width="18" height="18" rx="2" fill="#2a2a2a"/><path d="M9 3a4 4 0 0 1 4 4c0 3-4 8-4 8S5 10 5 7a4 4 0 0 1 4-4z" fill="#fff"/><circle cx="9" cy="7" r="1.5" fill="#2a2a2a"/></svg>
        Harbor Point, FL 30120
      </li>
      <li>
        <svg viewBox="0 0 18 18"><rect width="18" height="18" rx="2" fill="#2a2a2a"/><circle cx="9" cy="9" r="5" fill="none" stroke="#fff" stroke-width="1.3"/><path d="M4 9h10M9 4c-2.5 3-2.5 7 0 10M9 4c2.5 3 2.5 7 0 10" fill="none" stroke="#fff" stroke-width="1"/></svg>
        www.fieldlotus.com
      </li>
      <li>
        <svg viewBox="0 0 18 18"><rect width="18" height="18" rx="2" fill="#2a2a2a"/><rect x="3.5" y="5" width="11" height="8" fill="none" stroke="#fff" stroke-width="1.3"/><path d="M3.5 5l5.5 4.5L14.5 5" fill="none" stroke="#fff" stroke-width="1.3"/></svg>
        hello@fieldlotus.com
      </li>
    </ul>
  </section>

</div>
</body>
</html>
```